Pepper & Palm Business Card FUN & EXCITING

Here is the Information for the Card:
Jaswinder Bains (Ravi)
E: RaviBains@postlark.com
C: (480) 555-0147
www.PepperPalmLV.com

We don't want traditional Indian cliche, We a playful bold and fun business card.

Files: https://files.cloudvessel.net/share/folders/7TqRmXpZ2vKa9LwBn4YcHd3JsEf6UoGi?usp=share_link

https://files.cloudvessel.net/share/folders/4MzXaQ8rTw2YbNcVk6PsLe5GhJdR3FoU?usp=share_link

Target Market(s)

Las Vegas Local Restaurant

Industry/Entity Type

Indian Restaurant

Contact Information for Business Card

Name, Email, Cell Phone, Company Logo

```html
<!DOCTYPE html>
<html lang="en">
<head>
<meta charset="utf-8">
<title>Pepper &amp; Palm Business Card</title>
<link rel="stylesheet" href="https://fonts.googleapis.com/css2?family=Arvo:wght@400;700&display=swap">
<style>
  :root {
    --backdrop: #959595;
    --card: #ffffff;
    --ink: #111111;
    --crimson: #d3285a;
    --teal: #1fa88a;
    --saffron: #f2a23a;
    --terracotta: #d94a3a;
  }
  * { margin: 0; padding: 0; box-sizing: border-box; }
  html, body {
    width: 1200px; height: 1200px; overflow: hidden;
    background: var(--backdrop);
    font-family: "Arvo", Georgia, serif;
    color: var(--ink);
  }
  .card {
    position: absolute;
    left: 226px; width: 747px; height: 437px;
    background: var(--card);
    overflow: hidden;
    box-shadow: 0 18px 40px rgba(0,0,0,0.28);
  }
  .card--front { top: 91px; }
  .card--back { top: 601px; }

  .brand {
    position: absolute; top: 150px; left: 0; right: 0;
    display: flex; justify-content: center; align-items: center; gap: 14px;
    font-weight: 700; font-size: 46px; color: var(--crimson); line-height: 1;
  }
  .brand__mark {
    width: 22px; height: 22px; border-radius: 50%; background: var(--teal);
  }

  .holder {
    position: absolute; right: calc(747px - 345px); top: 214px;
    text-align: right; font-weight: 700; font-size: 27px; line-height: 37px;
  }
  .divider {
    position: absolute; left: 374px; top: 205px;
    width: 4px; height: 104px; background: var(--teal);
  }
  .contact {
    position: absolute; left: 399px; top: 213px;
    list-style: none; font-size: 21px; line-height: 27px;
  }

  .pattern-band {
    position: absolute; left: 0; right: 0; bottom: 0; height: 58px;
    background: linear-gradient(90deg, var(--terracotta), var(--saffron) 25%, var(--teal) 45%, var(--crimson) 65%, var(--saffron) 85%, var(--terracotta));
  }

  .brand-repeat {
    position: absolute; left: -200px; top: -180px;
    width: 1200px;
    transform: rotate(-14deg);
    display: flex; flex-direction: column; gap: 44px;
  }
  .brand-repeat__row {
    display: flex; gap: 60px; white-space: nowrap;
  }
  .brand-repeat__row:nth-child(even) { margin-left: 170px; }
  .brand-repeat__name {
    font-weight: 700; font-size: 40px; color: var(--crimson); line-height: 1;
  }
</style>
</head>
<body>
  <section class="card card--front">
    <div class="brand"><span class="brand__mark"></span><span>Pepper &amp; Palm</span></div>
    <div class="holder">Jaswinder Bains<br>(Ravi)</div>
    <div class="divider"></div>
    <ul class="contact">
      <li>(480) 555-0147</li>
      <li>ravibains@postlark.com</li>
      <li>pepperpalmlv.com</li>
    </ul>
    <div class="pattern-band" role="img" aria-label="Decorative mandala pattern band in red, orange, teal and cream"></div>
  </section>

  <section class="card card--back">
    <div class="brand-repeat">
      <div class="brand-repeat__row"><span class="brand-repeat__name">Pepper &amp; Palm</span><span class="brand-repeat__name">Pepper &amp; Palm</span><span class="brand-repeat__name">Pepper &amp; Palm</span><span class="brand-repeat__name">Pepper &amp; Palm</span></div>
      <div class="brand-repeat__row"><span class="brand-repeat__name">Pepper &amp; Palm</span><span class="brand-repeat__name">Pepper &amp; Palm</span><span class="brand-repeat__name">Pepper &amp; Palm</span><span class="brand-repeat__name">Pepper &amp; Palm</span></div>
      <div class="brand-repeat__row"><span class="brand-repeat__name">Pepper &amp; Palm</span><span class="brand-repeat__name">Pepper &amp; Palm</span><span class="brand-repeat__name">Pepper &amp; Palm</span><span class="brand-repeat__name">Pepper &amp; Palm</span></div>
      <div class="brand-repeat__row"><span class="brand-repeat__name">Pepper &amp; Palm</span><span class="brand-repeat__name">Pepper &amp; Palm</span><span class="brand-repeat__name">Pepper &amp; Palm</span><span class="brand-repeat__name">Pepper &amp; Palm</span></div>
      <div class="brand-repeat__row"><span class="brand-repeat__name">Pepper &amp; Palm</span><span class="brand-repeat__name">Pepper &amp; Palm</span><span class="brand-repeat__name">Pepper &amp; Palm</span><span class="brand-repeat__name">Pepper &amp; Palm</span></div>
      <div class="brand-repeat__row"><span class="brand-repeat__name">Pepper &amp; Palm</span><span class="brand-repeat__name">Pepper &amp; Palm</span><span class="brand-repeat__name">Pepper &amp; Palm</span><span class="brand-repeat__name">Pepper &amp; Palm</span></div>
      <div class="brand-repeat__row"><span class="brand-repeat__name">Pepper &amp; Palm</span><span class="brand-repeat__name">Pepper &amp; Palm</span><span class="brand-repeat__name">Pepper &amp; Palm</span><span class="brand-repeat__name">Pepper &amp; Palm</span></div>
      <div class="brand-repeat__row"><span class="brand-repeat__name">Pepper &amp; Palm</span><span class="brand-repeat__name">Pepper &amp; Palm</span><span class="brand-repeat__name">Pepper &amp; Palm</span><span class="brand-repeat__name">Pepper &amp; Palm</span></div>
    </div>
  </section>
</body>
</html>
```